Consulting Company PowerPoint Template Design

We are looking for an updated PowerPoint template design or our 55 person energy consulting firm (K7) based in San Francisco (www.kseven-example.com). We would like two versions of the same PowerPoint template in a 16:9 and 4:3 format with our existing logo.

We have an existing color scheme and template and are seeking your help to polish/update the template design for wide format and create a flexible template that is easy to use with content from Excel and Word. Our current template, and a couple of examples that we like are attached.

Specific requests include:

• Dark background for slide title
• A narrow section header
• Maximizing white space for content
• A limited number of well designed Master template layouts to choose from
• A selection of title and section header slides that are not San Francisco specific with some variety to chose from ideally with a focus on energy or nature, graphics/visuals.

For examples of energy specific templates see:
https://www.brightslidehub.example/energy/powerpoint-templates/0.html

Requirements
Must have
• Must use our logo but open to other designs, fonts, and styles for the PowerPoint template.
• Please use our existing color scheme found in the attached Excel file.
• Also we would like the ability to easily copy and paste from our existing/original template to the new template. In other words we would like backward compatibility to apply the new template format to our old PowerPoints that use our existing template.

```html
<!DOCTYPE html>
<html lang="en">
<head>
<meta charset="utf-8">
<title>Our Organise Chart</title>
<link href="https://fonts.googleapis.com/css2?family=Titillium+Web:wght@600;700&family=Arimo:wght@400;700&display=swap" rel="stylesheet">
<style>
:root{
  --navy:#0e4b6c;
  --title:#1b5a7e;
  --gold:#e3b25e;
  --gold-light:#f6e7cb;
  --red:#e2293d;
  --orange:#f2a43a;
  --frame:#2f62a3;
  --line:#c9c9c9;
  --ink:#222;
  --bg:#ffffff;
  --placeholder:#e4e9ee;
}
*{box-sizing:border-box;margin:0;padding:0}
html,body{width:1200px;height:900px;overflow:hidden;background:var(--bg)}
.slide{position:relative;width:1200px;height:900px;background:var(--bg);font-family:"Arimo",Arial,sans-serif;color:var(--ink)}
.title-accent{position:absolute;left:0;top:27px;width:12px;height:60px;background:var(--gold)}
.slide-title{position:absolute;left:26px;top:22px;font-family:"Titillium Web",sans-serif;font-weight:600;font-size:42px;color:var(--title);line-height:1.2}
.brand{position:absolute;right:20px;top:10px;display:flex;align-items:center;gap:12px}
.brand-name{font-family:"Titillium Web",sans-serif;font-weight:700;font-size:28px;color:var(--navy)}
.brand-dot{width:66px;height:66px;border-radius:50%;background:var(--navy)}
.connectors{position:absolute;left:0;top:0}
.child,.head{position:absolute;background:#fff;text-align:center}
.child{width:166px;height:42px;border:1.5px solid var(--red);font-weight:700;font-size:15px;line-height:39px}
.head{width:200px;height:64px;border:1.5px solid var(--orange);padding-top:12px}
.head-title{font-weight:700;font-size:15px;line-height:18px}
.head-dept{font-size:14px;line-height:18px;color:#333}
.leader{position:absolute;left:486px;top:304px;width:215px;height:197px;border:4.5px solid var(--frame);background:#fff;display:flex;align-items:center;justify-content:center}
.leader-photo{width:96px;height:96px;border-radius:50%;background:var(--placeholder)}
.footer{position:absolute;left:0;top:855px;width:1200px;height:45px;background:var(--navy)}
.footer-name{position:absolute;left:14px;top:0;line-height:45px;color:#fff;font-weight:700;font-size:21px}
.page-tab{position:absolute;right:0;top:0}
.page-number{position:absolute;right:20px;top:0;line-height:45px;font-size:24px;color:var(--gold);font-family:"Titillium Web",sans-serif}
</style>
</head>
<body>
<main class="slide">
  <div class="title-accent"></div>
  <h1 class="slide-title">Our Organise Chart</h1>
  <div class="brand"><span class="brand-name">K7</span><span class="brand-dot"></span></div>

  <svg class="connectors" width="1200" height="900" viewBox="0 0 1200 900" fill="none" stroke="var(--line)" stroke-width="1.5">
    <!-- left brackets -->
    <path d="M190 250H208V301H190M208 276H226"/>
    <path d="M190 376H208V429H190M208 403H226"/>
    <path d="M190 504H208V556H190M208 531H226"/>
    <path d="M190 621H208V673H190M208 648H226"/>
    <path d="M190 739H208V792H190M208 767H226"/>
    <!-- right brackets -->
    <path d="M998 250H980V301H998M980 276H960"/>
    <path d="M998 376H980V429H998M980 403H960"/>
    <path d="M998 504H980V556H998M980 531H960"/>
    <path d="M998 621H980V673H998M980 648H960"/>
    <path d="M998 739H980V792H998M980 767H960"/>
    <!-- to leader -->
    <path d="M327 309V333H486"/>
    <path d="M426 403H486"/>
    <path d="M574 501V767M426 531H574M426 648H574M426 767H574"/>
    <path d="M862 309V333H701"/>
    <path d="M760 403H701"/>
    <path d="M701 468H862V500"/>
    <path d="M618 501V767H760M618 648H760"/>
  </svg>

  <div class="child" style="left:24px;top:229px">CHILD 1</div>
  <div class="child" style="left:24px;top:280px">CHILD 2</div>
  <div class="child" style="left:24px;top:355px">CHILD 1</div>
  <div class="child" style="left:24px;top:408px">CHILD 2</div>
  <div class="child" style="left:24px;top:483px">CHILD 1</div>
  <div class="child" style="left:24px;top:535px">CHILD 2</div>
  <div class="child" style="left:24px;top:600px">CHILD 1</div>
  <div class="child" style="left:24px;top:652px">CHILD 2</div>
  <div class="child" style="left:24px;top:718px">CHILD 1</div>
  <div class="child" style="left:24px;top:771px">CHILD 2</div>

  <div class="head" style="left:226px;top:244px"><div class="head-title">HEAD 2</div><div class="head-dept">Department Name</div></div>
  <div class="head" style="left:226px;top:371px"><div class="head-title">HEAD3</div><div class="head-dept">Department Name</div></div>
  <div class="head" style="left:226px;top:499px"><div class="head-title">HEAD 4</div><div class="head-dept">Department Name</div></div>
  <div class="head" style="left:226px;top:616px"><div class="head-title">HEAD 5</div><div class="head-dept">Department Name</div></div>
  <div class="head" style="left:226px;top:735px"><div class="head-title">HEAD 5</div><div class="head-dept">Department Name</div></div>

  <div class="leader"><div class="leader-photo" role="img" aria-label="Profile photo of the team leader"></div></div>

  <div class="head" style="left:760px;top:244px"><div class="head-title">HEAD 6</div><div class="head-dept">Department Name</div></div>
  <div class="head" style="left:760px;top:371px"><div class="head-title">HEAD 7</div><div class="head-dept">Department Name</div></div>
  <div class="head" style="left:760px;top:499px"><div class="head-title">HEAD 8</div><div class="head-dept">Department Name</div></div>
  <div class="head" style="left:760px;top:616px"><div class="head-title">HEAD 9</div><div class="head-dept">Department Name</div></div>
  <div class="head" style="left:760px;top:735px"><div class="head-title">HEAD 9</div><div class="head-dept">Department Name</div></div>

  <div class="child" style="left:998px;top:229px">CHILD 1</div>
  <div class="child" style="left:998px;top:280px">CHILD 2</div>
  <div class="child" style="left:998px;top:355px">CHILD 1</div>
  <div class="child" style="left:998px;top:408px">CHILD 2</div>
  <div class="child" style="left:998px;top:483px">CHILD 1</div>
  <div class="child" style="left:998px;top:535px">CHILD 2</div>
  <div class="child" style="left:998px;top:600px">CHILD 1</div>
  <div class="child" style="left:998px;top:652px">CHILD 2</div>
  <div class="child" style="left:998px;top:718px">CHILD 1</div>
  <div class="child" style="left:998px;top:771px">CHILD 2</div>

  <footer class="footer">
    <span class="footer-name">Kestrel Seven Energy Advisors</span>
    <svg class="page-tab" width="100" height="45" viewBox="0 0 100 45">
      <polygon points="6,0 100,0 100,45 22,45" fill="var(--gold)"/>
      <polygon points="14,0 100,0 100,45 30,45" fill="var(--gold-light)"/>
    </svg>
    <span class="page-number">1</span>
  </footer>
</main>
</body>
</html>
```